WE ARE BRIGHT SPARROW, building a full website with ecommerce

requirements:
CODED FOR SITEQUILL
ONLINE STORE FUNCTION WITH E-COMMERCE USING TRADEBLOOM
PAGEWAVE AND PICTOLANE LINKS

I need a website design for my organization, WE ARE BRIGHT SPARROW, a global empowerment movement elevating woman, and the world. The site's home page should reflect our mission, to empower women. It should have a strong, empowering feel, with minimalistic design.
Please see www.lunavelto.com and http://www.corvenhal.co/ for an inspiration on layout and feel.

**PLEASE SEE ATTACHMENT "LOGO MOCK UP" FOR LOGO. THIS IS NOT THE FINAL VECTOR FILE, BUT THIS LOOKS THE SAME AS THE FINAL LOGO.

HOME PAGE:
The first section of the home page should include a background image with our logo center.

You should include the following links to pages at the top right of the page:
MISSION
MANTRA
ARMOR
MEET BS (I would like "bs" to be our logo)
pagewave and pictolane links

As you scroll down the page, you should see the following sections, which correlate to the links to pages as written above. **SEE ATTACHED SKETCH "HOMEPAGE LAYOUT IDEA" FOR REFERENCE**

WHO WE ARE (correlates to the link Mission)

OUR MANTRA (correlates to the link Mantra)

OUR ARMOR (correlates to the link The Shirt)
(This is where we will sell a shirt (and other apparel) and need the e-commerce function)

MEET BRIGHT SPARROWS (correlates to the link Meet BS)

SHOW OFF YOUR SUPER POWERS (correlates to the pagewave and pictolane)

FEATURED BRIGHT SPARROW (no link on top right of page)

On the homepage, for each of the above sections, as you scroll down there should be an image, either in the background or framed, next to the title (WHO WE ARE, for example), as well as one sentence of small text explaining the title. The title (WHO WE ARE) and the one sentence should link to a page (ie WHO WE ARE + the one sentence links to the MISSION page). ** SEE ATTACHED SKETCH "HOMEPAGE SECTION IDEAS" FOR REFERENCE**

**PLEASE SEE ATTACHMENT "WEBSITE TITLE IDEAS" FOR A STARTING PLACE OF THE LOOK. These don't have to be exact, but they give you an idea of what I'm looking for.

**FONTS TYPOLD EXTRA BOLD AND TYPOLD BOOK 500 (WHICH SHOULD BE BOLDED MANUALLY) ARE ATTACHED**

Target Market(s)

Women, mainly in US

Industry/Entity Type

Social

Coding

Coded - Design and coding required

Number of Pages Required

5+ page

Font styles to use
Other font styles liked:
• Typol Extra Bold

Requirements
Must have
• CODED FOR SITEQUILL
• ONLINE STORE FUNCTION WITH E-COMMERCE USING TRADEBLOOM
• PAGEWAVE AND PICTOLANE LINKS
• Typold Extra Bold and Typold Book 500, attached
• please see description for all requirements
Nice to have
• please see description for all ideas
Should not have

```html
<!DOCTYPE html>
<html lang="en">
<head>
<meta charset="utf-8">
<title>We Are Bright Sparrow</title>
<link href="https://fonts.googleapis.com/css2?family=Montserrat:wght@400;500;600;700;800;900&display=swap" rel="stylesheet">
<style>
:root{
  --ink:#111111;
  --white:#ffffff;
  --panel:#f0f0f0;
  --band:#e2e2e2;
  --muted:#777777;
  --line:#cfcfcf;
  --footer:#000000;
  --hero-a:#8f8a84;
  --hero-b:#c9c3bb;
  --shirt-grey:#b9b9bd;
  --shirt-coral:#f07b74;
  --shirt-blue:#5aa3ef;
  --shirt-green:#7dde5d;
}
*{margin:0;padding:0;box-sizing:border-box}
html,body{width:1200px;height:3689px;overflow:hidden}
body{font-family:'Montserrat',sans-serif;color:var(--ink);background:var(--white);position:relative}
a{color:inherit;text-decoration:none}

/* header */
.site-header{height:101px;display:flex;align-items:center;justify-content:space-between;padding:0 133px}
.brand{display:flex;align-items:center;gap:12px;font-weight:800;font-size:20px;line-height:1;letter-spacing:.5px}
.brand-square{width:30px;height:30px;background:var(--ink)}
.main-nav{display:flex;align-items:center;gap:44px;font-size:13px;font-weight:700;letter-spacing:.5px}
.main-nav a{color:#9a9a9a}
.main-nav a.is-active{color:var(--ink)}
.social-mini{display:flex;gap:10px}
.social-mini a{font-size:10px;color:#9a9a9a;border:1px solid var(--line);padding:6px 7px;letter-spacing:.5px}

/* hero */
.hero{position:relative;height:514px;background:linear-gradient(120deg,var(--hero-a),var(--hero-b) 55%,#8b8780);display:flex;flex-direction:column;align-items:center;justify-content:center;color:var(--white);text-align:center}
.hero-title{font-size:40px;font-weight:800;letter-spacing:1px;line-height:1.1;margin-top:20px}
.hero-sub{font-size:21px;font-weight:800;letter-spacing:.5px;margin-top:6px}
.signup{display:flex;margin-top:22px}
.signup input{width:353px;height:47px;border:0;padding:0 18px;font:500 15px 'Montserrat',sans-serif;color:var(--ink)}
.signup button{width:122px;height:47px;border:0;background:var(--ink);color:var(--white);font:800 15px 'Montserrat',sans-serif;letter-spacing:.5px}
.hero-arrow{position:absolute;top:238px;width:24px;height:30px}
.hero-arrow.prev{left:28px}.hero-arrow.next{right:28px}

/* mission statement */
.statement{height:330px;text-align:center;padding-top:78px}
.statement h1{font-size:30px;font-weight:800;letter-spacing:1px;line-height:1.4}
.statement h1 span{display:block;font-weight:500}
.lets-fly{display:inline-flex;align-items:center;gap:14px;margin-top:22px;font-size:38px;font-weight:900;line-height:.9;text-align:left}
.mark{background:var(--ink);display:inline-block;flex:none}
.lets-fly .mark{width:56px;height:56px}

/* feature rows */
.feature{display:flex;height:400px}
.feature-text{width:600px;background:var(--panel);padding:0 133px;display:flex;flex-direction:column;justify-content:center}
.feature.reverse .feature-text{background:var(--white);padding:0 70px 0 34px}
.feature-photo{width:600px;height:400px}
.section-title{display:flex;align-items:center;gap:14px;font-size:28px;font-weight:900;line-height:.95;letter-spacing:.3px;margin-bottom:28px}
.section-title .mark{width:54px;height:54px}
.feature p{font-size:12.5px;line-height:1.75;color:#222}
.photo-meeting{background:linear-gradient(110deg,#3b302a,#9b7a62 45%,#d9cfc4 70%,#4a4440)}
.photo-team{background:linear-gradient(100deg,#e9e9e9,#c9d4e3 45%,#f2f2f2 75%,#dfdfdf)}
.photo-crowd{background:linear-gradient(95deg,#6a5547,#c3a07b 45%,#b77b5f 70%,#3d3a32)}

/* armor */
.armor{height:565px;padding-top:80px}
.center-title{justify-content:center}
.products{display:flex;gap:22px;padding:0 133px;margin-top:30px}
.product{width:216px;text-align:center}
.shirt{height:220px}
.shirt.grey{background:radial-gradient(circle at 50% 45%,var(--shirt-grey),#e8e8e8 75%)}
.shirt.coral{background:radial-gradient(circle at 50% 45%,var(--shirt-coral),#f3e3e2 75%)}
.shirt.blue{background:radial-gradient(circle at 50% 45%,var(--shirt-blue),#dfe9f4 75%)}
.shirt.green{background:radial-gradient(circle at 50% 45%,var(--shirt-green),#e3f2dc 75%)}
.product-name{font-size:17px;font-weight:500;margin-top:16px}
.product-price{font-size:12px;font-weight:600;margin-top:6px}
.cart{display:block;margin:10px auto 0;width:18px;height:16px}

/* social band */
.social-band{height:195px;background:var(--band);display:flex;align-items:center;justify-content:center;gap:30px}
.social-band .section-title{margin:0}
.social-link{display:flex;align-items:center;gap:8px;font-size:13px;font-weight:800}
.social-link .dot{width:30px;height:30px;border-radius:50%;background:var(--ink)}

/* featured */
.featured{height:470px;padding-top:72px}
.people{display:flex;gap:33px;padding:0 133px;margin-top:14px}
.person{width:160px;text-align:center}
.portrait{height:160px;background:linear-gradient(180deg,#b9b4ae,#6d6660)}
.portrait.alt{background:linear-gradient(180deg,#d6d3cf,#8f8a85)}
.person-name{font-size:12px;margin-top:10px}
.person-role{font-size:9px;color:var(--muted);margin-top:5px}

/* footer */
.site-footer{height:314px;background:var(--footer);color:var(--white);text-align:center;padding-top:62px}
.footer-brand{font-size:22px;font-weight:800;letter-spacing:1px}
.footer-nav{display:flex;justify-content:center;gap:44px;font-size:13px;font-weight:800;letter-spacing:.5px;margin-top:48px}
.copyright{font-size:12px;color:#cfcfcf;margin-top:24px;letter-spacing:.3px}
.footer-social{display:flex;justify-content:center;gap:14px;margin-top:24px}
.footer-social a{font-size:10px;border:1px solid #777;padding:6px 8px;letter-spacing:.5px}
</style>
</head>
<body>

<header class="site-header">
  <a class="brand" href="#"><span class="brand-square"></span>BRIGHT SPARROW</a>
  <nav class="main-nav">
    <a class="is-active" href="#mission">MISSION</a>
    <a href="#mantra">MANTRA</a>
    <a href="#meet">MEET BS</a>
    <a href="#armor">THE SHIRT</a>
    <span class="social-mini"><a href="#">PAGEWAVE</a><a href="#">PICTOLANE</a></span>
  </nav>
</header>

<section class="hero" role="img" aria-label="Photo of smiling women gathered around a meeting table">
  <svg class="hero-arrow prev" viewBox="0 0 24 30"><polyline points="16,6 8,15 16,24" fill="none" stroke="#fff" stroke-width="3"/></svg>
  <svg class="hero-arrow next" viewBox="0 0 24 30"><polyline points="8,6 16,15 8,24" fill="none" stroke="#fff" stroke-width="3"/></svg>
  <h2 class="hero-title">WE ARE BRIGHT SPARROW</h2>
  <p class="hero-sub">AND I WILL CONQUER THE WORLD</p>
  <form class="signup">
    <input type="email" value="hello@brightsparrows.org" aria-label="Email">
    <button type="button">LET'S FLY</button>
  </form>
</section>

<section class="statement">
  <h1>WE ARE BRIGHT SPARROW IS A GLOBAL EMPOWERMENT<span>MOVEMENT ELEVATING WOMEN... AND THE WORLD</span></h1>
  <div class="lets-fly"><span class="mark"></span><span>LET'S<br>FLY</span></div>
</section>

<section class="feature" id="mission">
  <div class="feature-text">
    <h2 class="section-title"><span class="mark"></span><span>WHO<br>WE<br>ARE</span></h2>
    <p>Suspendisse gravida ornare erat sed pulvinar. Vestibulum luctus ex in egestas fringilla. Fusce nec leo ac urna pulvinar auctor. Mauris bibendum fringilla velit. Nulla in lorem at massa pellentesque posuere. Nulla tristique posuere molestie. Aliquam erat volutpat. Etiam quis aliquet risus. Duis ornare erat eget magna dapibus, in accumsan quam pharetra.</p>
  </div>
  <div class="feature-photo photo-meeting" role="img" aria-label="Photo of women talking together in an office lounge"></div>
</section>

<section class="feature reverse" id="mantra">
  <div class="feature-photo photo-team" role="img" aria-label="Photo of three confident women standing with arms crossed"></div>
  <div class="feature-text">
    <h2 class="section-title"><span class="mark"></span><span>OUR<br>MANTRA</span></h2>
    <p>Nam tempus, quam in bibendum vulputate, sapien dolor viverra nisl, vitae euismod elit turpis et nulla. Aliquam erat volutpat. Pellentesque blandit lacus eget nunc faucibus, et tincidunt eros viverra. Phasellus consequat sagittis nisi suscipit feugiat. Cras eget leo sed nunc hendrerit ultricies eu at nisl. Praesent iaculis faucibus urna sit amet lacinia. Maecenas consequat justo enim.</p>
  </div>
</section>

<section class="feature" id="meet">
  <div class="feature-text">
    <h2 class="section-title"><span class="mark"></span><span>MEET<br>BRIGHT<br>SPARROWS</span></h2>
    <p>Fusce eget neque elit. Sed augue orci, elementum in magna congue, tincidunt vulputate erat. Aliquam consectetur orci molestie dictum molestie. Proin eget congue nulla, vel tempor diam. Ut non ante est. Vestibulum condimentum, risus ut posuere cursus, velit justo accumsan sem, lobortis aliquet metus dui eu libero. Pellentesque a imperdiet dolor, et auctor est.</p>
  </div>
  <div class="feature-photo photo-crowd" role="img" aria-label="Photo of a group of smiling women"></div>
</section>

<section class="armor" id="armor">
  <h2 class="section-title center-title"><span class="mark"></span><span>OUR<br>ARMOR</span></h2>
  <div class="products">
    <div class="product"><div class="shirt grey" role="img" aria-label="Grey t-shirt with the movement emblem"></div><p class="product-name">Fusce sollicitudin</p><p class="product-price">$18.00</p><svg class="cart" viewBox="0 0 18 16"><path d="M0 1h3l2.5 9h9.5l2-7H4.5" fill="none" stroke="#111" stroke-width="2"/><circle cx="7" cy="14" r="1.6"/><circle cx="14" cy="14" r="1.6"/></svg></div>
    <div class="product"><div class="shirt coral" role="img" aria-label="Coral t-shirt with the movement emblem"></div><p class="product-name">Proin placerat</p><p class="product-price">$18.00</p><svg class="cart" viewBox="0 0 18 16"><path d="M0 1h3l2.5 9h9.5l2-7H4.5" fill="none" stroke="#111" stroke-width="2"/><circle cx="7" cy="14" r="1.6"/><circle cx="14" cy="14" r="1.6"/></svg></div>
    <div class="product"><div class="shirt blue" role="img" aria-label="Blue t-shirt with the movement emblem"></div><p class="product-name">Aenean facilisis</p><p class="product-price">$18.00</p><svg class="cart" viewBox="0 0 18 16"><path d="M0 1h3l2.5 9h9.5l2-7H4.5" fill="none" stroke="#111" stroke-width="2"/><circle cx="7" cy="14" r="1.6"/><circle cx="14" cy="14" r="1.6"/></svg></div>
    <div class="product"><div class="shirt green" role="img" aria-label="Green t-shirt with the movement emblem"></div><p class="product-name">Etiam mattis</p><p class="product-price">$18.00</p><svg class="cart" viewBox="0 0 18 16"><path d="M0 1h3l2.5 9h9.5l2-7H4.5" fill="none" stroke="#111" stroke-width="2"/><circle cx="7" cy="14" r="1.6"/><circle cx="14" cy="14" r="1.6"/></svg></div>
  </div>
</section>

<section class="social-band">
  <h2 class="section-title"><span class="mark"></span><span>SHOW OFF YOUR<br>SUPER POWERS</span></h2>
  <a class="social-link" href="#"><span class="dot"></span>PAGEWAVE</a>
  <a class="social-link" href="#"><span class="dot"></span>PICTOLANE</a>
</section>

<section class="featured">
  <h2 class="section-title center-title"><span class="mark"></span><span>FEATURED<br>BRIGHT<br>SPARROWS</span></h2>
  <div class="people">
    <div class="person"><div class="portrait" role="img" aria-label="Portrait of Sophia"></div><p class="person-name">Sophia</p><p class="person-role">Aliquam dignissim</p></div>
    <div class="person"><div class="portrait alt" role="img" aria-label="Portrait of Emma"></div><p class="person-name">Emma</p><p class="person-role">Nulla porttitor</p></div>
    <div class="person"><div class="portrait" role="img" aria-label="Portrait of Olivia"></div><p class="person-name">Olivia</p><p class="person-role">Nam tempus</p></div>
    <div class="person"><div class="portrait alt" role="img" aria-label="Portrait of Isabella"></div><p class="person-name">Isabella</p><p class="person-role">Duis hendrerit</p></div>
    <div class="person"><div class="portrait" role="img" aria-label="Portrait of Emily"></div><p class="person-name">Emily</p><p class="person-role">Nam elementum</p></div>
  </div>
</section>

<footer class="site-footer">
  <p class="footer-brand">BRIGHT SPARROW</p>
  <nav class="footer-nav"><a href="#mission">MISSION</a><a href="#mantra">MANTRA</a><a href="#meet">MEET BS</a><a href="#armor">THE SHIRT</a></nav>
  <p class="copyright">Copyright &copy; 2017 We Are Bright Sparrow. All rights reserved.</p>
  <div class="footer-social"><a href="#">PAGEWAVE</a><a href="#">PICTOLANE</a></div>
</footer>

</body>
</html>
```